The Linen Loft Co

We need a business card design for our wardrobe company.
Please visit our website www.gentlelinenlofts.com to get an idea of who we are.

```html
<!DOCTYPE html>
<html lang="en">
<head>
<meta charset="utf-8">
<title>The Linen Loft Co – Business Card</title>
<link rel="stylesheet" href="https://fonts.googleapis.com/css2?family=Roboto:wght@400;500;700&display=swap">
<style>
  :root {
    --backdrop: #e7ddd3;
    --card: #ffffff;
    --ink: #111111;
    --ink-soft: #3d3d3d;
    --muted: #a6a6a6;
    --rule: #c9c9c9;
  }
  html, body {
    margin: 0;
    padding: 0;
    width: 1200px;
    height: 989px;
    overflow: hidden;
    background: var(--backdrop);
    font-family: "Roboto", Arial, sans-serif;
  }
  .card {
    position: absolute;
    left: 50px;
    top: 178px;
    width: 1100px;
    height: 632px;
    background: var(--card);
    box-shadow: 0 6px 22px rgba(0, 0, 0, 0.25);
  }
  .brand {
    position: absolute;
    left: 92px;
    top: 284px;
    display: flex;
    align-items: center;
    gap: 16px;
  }
  .brand-mark {
    width: 76px;
    height: 76px;
    flex: none;
  }
  .brand-text {
    display: flex;
    flex-direction: column;
    align-items: center;
    gap: 10px;
  }
  .brand-name {
    font-weight: 500;
    font-size: 22px;
    color: var(--ink);
    text-transform: uppercase;
    letter-spacing: 0.2px;
  }
  .brand-tagline {
    font-weight: 500;
    font-size: 18px;
    color: var(--ink);
  }
  .divider {
    position: absolute;
    left: 557px;
    top: 178px;
    width: 2px;
    height: 290px;
    background: linear-gradient(to bottom, rgba(201,201,201,0), var(--rule) 15%, var(--rule) 85%, rgba(201,201,201,0));
  }
  .details {
    position: absolute;
    left: 586px;
    top: 180px;
    color: var(--ink-soft);
  }
  .person-name {
    margin: 0;
    font-weight: 700;
    font-size: 42px;
    line-height: 48px;
    color: var(--ink);
  }
  .person-role {
    margin: 0;
    font-weight: 500;
    font-size: 28px;
    line-height: 32px;
    color: var(--muted);
  }
  .address {
    margin: 20px 0 0;
    font-style: normal;
    font-size: 26px;
    line-height: 34px;
  }
  .contacts {
    list-style: none;
    margin: 12px 0 0;
    padding: 0;
    font-size: 26px;
    line-height: 34px;
  }
  .contacts li {
    display: flex;
    align-items: center;
    gap: 12px;
  }
  .contacts svg {
    width: 24px;
    height: 24px;
    flex: none;
    fill: var(--ink);
  }
</style>
</head>
<body>
  <main class="card">
    <div class="brand">
      <svg class="brand-mark" viewBox="0 0 76 76" aria-hidden="true">
        <rect x="3" y="3" width="70" height="70" fill="none" stroke="#111" stroke-width="4"/>
      </svg>
      <div class="brand-text">
        <span class="brand-name">The Linen Loft Co</span>
        <span class="brand-tagline">Made to Fit Every Room</span>
      </div>
    </div>

    <div class="divider"></div>

    <section class="details">
      <h1 class="person-name">Daniel Harper</h1>
      <p class="person-role">President</p>
      <address class="address">Arden Court, 42 Mill Lane,<br>London N4 7QS</address>
      <ul class="contacts">
        <li>
          <svg viewBox="0 0 24 24" aria-hidden="true"><path d="M6.6 10.8c1.4 2.8 3.8 5.1 6.6 6.6l2.2-2.2c.3-.3.7-.4 1-.2 1.1.4 2.3.6 3.6.6.6 0 1 .4 1 1V20c0 .6-.4 1-1 1C10.6 21 3 13.4 3 4c0-.6.4-1 1-1h3.5c.6 0 1 .4 1 1 0 1.3.2 2.5.6 3.6.1.3 0 .7-.2 1z"/></svg>
          <span>020 7946 0318</span>
        </li>
        <li>
          <svg viewBox="0 0 24 24" aria-hidden="true"><path d="M2 6h20v13H2zM4 8v.4l8 5.2 8-5.2V8zm0 2.8V17h16v-6.2l-8 5.2z"/></svg>
          <span>info@gentlelinenlofts.com</span>
        </li>
        <li>
          <svg viewBox="0 0 24 24" aria-hidden="true"><path d="M12 2a10 10 0 1 0 0 20 10 10 0 0 0 0-20zm-1 17.9A8 8 0 0 1 4.2 10.2L9 15v1a2 2 0 0 0 2 2zm6.9-2.5A2 2 0 0 0 16 16h-1v-3a1 1 0 0 0-1-1H8v-2h2a1 1 0 0 0 1-1V7h2a2 2 0 0 0 2-2v-.4a8 8 0 0 1 2.9 12.8z"/></svg>
          <span>www.gentlelinenlofts.com</span>
        </li>
      </ul>
    </section>
  </main>
</body>
</html>
```